Used Semi Truck Website Redesign

We are redoing the website backend and would like to also do a front end redesign. I would like a Mobile and Desktop mockup for each page. The website has more mobile visitors than desktop visitors. Our competitor is http://www.haulwaybazaar.example. We don't want to copy them exactly but we want a site that looks more like that. We need the functionality of that site. One big difference is that we also sell parts and trailers.

We need a redesign for front page, product detail page, search result page, content page. It is very important that the site is very easy to use on mobile devices. Our target audience is Truck drivers.

Feel free to use demo fonts stock images, and icons. We will purchase necessary 3rd party media when a winner is chosen.

Target Market(s)

People who want to buy used trucks.

Coding

Coded - Design and coding required

Number of Pages Required

5+ page

Requirements
Must have
• Mockup for Desktop and Mobile pages.

```html
<!DOCTYPE html>
<html lang="en">
<head>
<meta charset="utf-8">
<title>Ridgeline trucks</title>
<link href="https://fonts.googleapis.com/css2?family=Open+Sans:wght@400;600;700&display=swap" rel="stylesheet">
<style>
:root{
  --blue:#0a6bb8;
  --blue-dark:#075a9c;
  --orange:#e8501e;
  --panel:#dde8f7;
  --band:#f1f1f1;
  --text:#444;
  --muted:#666;
  --line:#d6d6d6;
  --white:#fff;
}
*{box-sizing:border-box;margin:0;padding:0}
html,body{width:1200px;height:2206px;overflow:hidden}
body{position:relative;font-family:'Open Sans',sans-serif;color:var(--text);background:var(--white);font-size:12px}
.abs{position:absolute}
a{color:var(--blue)}
.topbar{left:0;top:0;width:1200px;height:26px;background:var(--blue)}
.topbar span{position:absolute;top:6px;color:var(--white);font-size:11px}
.topbar i{position:absolute;top:0;width:1px;height:26px;background:rgba(255,255,255,.35)}
.logo{font-weight:700;color:var(--blue);font-size:38px;letter-spacing:-.5px}
.hbtn{height:41px;border:2px solid;display:flex;align-items:center;justify-content:center;font-size:16px;gap:8px}
.hbtn.find{border-color:var(--blue);color:var(--blue)}
.hbtn.sell{border-color:var(--orange);color:var(--orange)}
.hbtn.research{border-color:#999;color:#777}
.quick{left:0;top:132px;width:1200px;height:96px;background:var(--band)}
.label-title{font-weight:700;color:var(--blue);text-transform:uppercase}
.field{top:175px;height:37px;background:var(--white);border:1px solid #ccc;font-size:10px;padding:0 10px;display:flex;align-items:center;justify-content:space-between;color:#444}
.field b{width:0;height:0;border-left:5px solid transparent;border-right:5px solid transparent;border-top:6px solid #333}
.btn{background:var(--blue);color:var(--white);font-weight:700;display:flex;align-items:center;justify-content:center;text-transform:uppercase}
.hero{left:131px;top:260px;width:937px;height:386px;background:var(--panel)}
.tab{left:144px;width:240px;background:linear-gradient(#fff,#efefef);display:flex;align-items:center;padding-left:80px;font-size:14px;color:#555;line-height:1.5;text-transform:uppercase}
.tab.active{background:var(--blue);color:var(--white);font-weight:600}
.tab.active:after{content:"";position:absolute;right:-12px;top:32px;border-top:12px solid transparent;border-bottom:12px solid transparent;border-left:12px solid var(--blue)}
.tab svg{position:absolute;left:20px}
.kind{width:160px;height:164px;background:var(--white);display:flex;flex-direction:column;align-items:center;justify-content:flex-end;padding-bottom:26px;font-size:11px;text-align:center;color:#555;text-transform:uppercase;line-height:1.6}
.kind svg{margin-bottom:20px}
.types{left:790px;top:288px;width:260px}
.types h3{font-size:15px;color:var(--blue);font-weight:700;line-height:1.6}
.types ul{list-style:none;margin-top:26px}
.types li{font-size:13px;height:30px;padding-left:20px;position:relative;color:#555}
.types li:before{content:"";position:absolute;left:3px;top:6px;border-top:4px solid transparent;border-bottom:4px solid transparent;border-left:5px solid #333}
.section-title{font-size:16px;font-weight:700;color:var(--blue);text-transform:uppercase}
.ad{width:187px;height:269px;background:var(--panel);text-align:center}
.ad .photo{height:163px}
.ad h4{font-size:13px;color:var(--blue);margin-top:19px;font-weight:700;text-transform:uppercase}
.ad .price{font-size:13px;margin-top:14px}
.ad .loc{font-size:11px;margin-top:6px;color:#555}
.box{border:2px solid #e3e3e3;background:var(--white)}
.links{display:grid;font-size:11px;row-gap:6px}
.links a{height:18px}
.small-btn{font-size:10px;height:24px}
.blog-item .date{font-size:10px}
.blog-item h5{font-size:13px;color:var(--blue);font-weight:700;text-transform:uppercase;margin-top:8px}
.blog-item p{font-size:12px;line-height:1.85;margin-top:10px;color:#555}
.footer{left:0;top:1706px;width:1200px;height:500px;background:var(--band)}
.social{width:34px;height:34px;border:2px solid var(--blue);border-radius:50%;background:var(--white)}
.tweet h6{font-size:11px;color:var(--blue);font-weight:700}
.tweet p{font-size:11px;line-height:1.6;margin-top:6px;color:#555}
.tweet .when{position:absolute;right:16px;top:0;font-size:11px;color:#bbb}
.tweet .dot{position:absolute;left:22px;top:6px;width:40px;height:40px;border:2px solid var(--blue);border-radius:50%;background:var(--white);display:flex;align-items:center;justify-content:center}
.tweet .dot i{width:14px;height:14px;border-radius:50%;background:var(--blue)}
.foot-links{font-size:11px;color:#555}
</style>
</head>
<body>

<div class="abs topbar">
  <i style="left:750px"></i><i style="left:836px"></i><i style="left:962px"></i>
  <span style="left:655px">&#9679; My Trader</span>
  <span style="left:769px">&#9679; Login</span>
  <span style="left:854px">&#9679; Find a Dealer</span>
  <span style="left:981px">&#9679; Dealer Login</span>
</div>

<div class="abs logo" style="left:131px;top:50px">Ridgeline trucks</div>
<div class="abs hbtn find" style="left:654px;top:59px;width:122px">
  <svg width="14" height="14" viewBox="0 0 14 14"><circle cx="6" cy="6" r="4.2" fill="none" stroke="currentColor" stroke-width="2"/><path d="M9 9l4 4" stroke="currentColor" stroke-width="2"/></svg>Find</div>
<div class="abs hbtn sell" style="left:800px;top:59px;width:122px">
  <svg width="16" height="14" viewBox="0 0 16 14"><path d="M0 1h3l2 8h9l2-6H4" fill="currentColor"/><circle cx="6" cy="12" r="1.5" fill="currentColor"/><circle cx="13" cy="12" r="1.5" fill="currentColor"/></svg>Sell</div>
<div class="abs hbtn research" style="left:946px;top:59px;width:122px">
  <svg width="13" height="15" viewBox="0 0 13 15"><rect x="1" y="1" width="11" height="13" fill="none" stroke="currentColor" stroke-width="1.5"/><path d="M3 5h7M3 8h7M3 11h5" stroke="currentColor"/></svg>Research</div>

<div class="abs quick"></div>
<div class="abs label-title" style="left:103px;top:146px;font-size:12px">Quick Search</div>
<div class="abs field" style="left:104px;width:147px">Keyword</div>
<div class="abs field" style="left:260px;width:146px">Class<b></b></div>
<div class="abs field" style="left:413px;width:147px">Category<b></b></div>
<div class="abs field" style="left:568px;width:147px">Make<b></b></div>
<div class="abs field" style="left:720px;width:148px">Zip code<b></b></div>
<div class="abs field" style="left:876px;width:142px">Any Distance<b></b></div>
<div class="abs btn" style="left:1026px;top:175px;width:84px;height:37px;font-size:12px">Search</div>

<div class="abs hero"></div>
<div class="abs tab active" style="top:276px;height:86px">
  <svg width="46" height="22" viewBox="0 0 46 22"><rect x="2" y="3" width="28" height="11" rx="5" fill="#fff"/><rect x="31" y="5" width="11" height="9" fill="#fff"/><circle cx="10" cy="17" r="3" fill="#fff"/><circle cx="36" cy="17" r="3" fill="#fff"/></svg>
  Find heavy duty<br>trucks for sale</div>
<div class="abs tab" style="top:368px;height:79px">
  <svg width="40" height="22" viewBox="0 0 40 22"><rect x="2" y="2" width="20" height="13" fill="#777"/><path d="M23 6h8l5 5v4H23z" fill="#777"/><circle cx="9" cy="17" r="3" fill="#777"/><circle cx="31" cy="17" r="3" fill="#777"/></svg>
  Find medium duty<br>trucks for sale</div>
<div class="abs tab" style="top:451px;height:86px">
  <svg width="40" height="22" viewBox="0 0 40 22"><rect x="8" y="2" width="12" height="7" fill="#777"/><path d="M2 9h34v6H2z" fill="#777"/><circle cx="9" cy="17" r="3" fill="#777"/><circle cx="29" cy="17" r="3" fill="#777"/></svg>
  Find light duty<br>trucks for sale</div>
<div class="abs tab" style="top:538px;height:86px">
  <svg width="40" height="22" viewBox="0 0 40 22"><rect x="2" y="3" width="36" height="11" fill="#777"/><circle cx="8" cy="17" r="3" fill="#777"/><circle cx="15" cy="17" r="3" fill="#777"/><circle cx="32" cy="17" r="3" fill="#777"/></svg>
  Find truck<br>trailers for sale</div>

<div class="abs kind" style="left:409px;top:276px">
  <svg width="80" height="48" viewBox="0 0 80 48"><rect x="6" y="4" width="26" height="26" fill="var(--blue)"/><rect x="6" y="30" width="70" height="7" fill="var(--blue)"/><circle cx="18" cy="40" r="6" fill="var(--blue)" stroke="#fff" stroke-width="2"/><circle cx="64" cy="40" r="6" fill="var(--blue)" stroke="#fff" stroke-width="2"/></svg>
  Conventional<br>sleeper truck</div>
<div class="abs kind" style="left:591px;top:276px">
  <svg width="80" height="58" viewBox="0 0 80 58"><rect x="6" y="22" width="22" height="20" fill="var(--blue)"/><g transform="rotate(-25 50 20)"><rect x="34" y="8" width="34" height="22" rx="6" fill="var(--blue)"/></g><rect x="6" y="38" width="70" height="7" fill="var(--blue)"/><circle cx="18" cy="48" r="6" fill="var(--blue)" stroke="#fff" stroke-width="2"/><circle cx="64" cy="48" r="6" fill="var(--blue)" stroke="#fff" stroke-width="2"/></svg>
  Dump-truck</div>
<div class="abs kind" style="left:409px;top:460px">
  <svg width="80" height="48" viewBox="0 0 80 48"><rect x="8" y="6" width="20" height="24" fill="var(--blue)"/><rect x="6" y="30" width="70" height="7" fill="var(--blue)"/><circle cx="18" cy="40" r="6" fill="var(--blue)" stroke="#fff" stroke-width="2"/><circle cx="64" cy="40" r="6" fill="var(--blue)" stroke="#fff" stroke-width="2"/></svg>
  Conventional<br>day cab</div>
<div class="abs kind" style="left:591px;top:460px">
  <svg width="84" height="56" viewBox="0 0 84 56"><path d="M36 4v30M36 6l18 16" stroke="var(--blue)" stroke-width="3" fill="none"/><rect x="4" y="24" width="28" height="14" fill="var(--blue)"/><rect x="50" y="18" width="28" height="22" rx="8" fill="var(--blue)"/><rect x="4" y="36" width="74" height="6" fill="var(--blue)"/><circle cx="16" cy="46" r="6" fill="var(--blue)" stroke="#fff" stroke-width="2"/><circle cx="66" cy="46" r="6" fill="var(--blue)" stroke="#fff" stroke-width="2"/></svg>
  Wrecker<br>tow truck</div>

<div class="abs types">
  <h3>What Type Heavy Duty Truck<br>do you need?</h3>
  <ul>
    <li>Cab-Chassis</li><li>Flatbed-Truck</li><li>Box Truck-Straight Truck</li><li>Day Cab</li><li>Tractor</li><li>Crane Truck</li><li>Bucket Truck - Boom Truck</li>
  </ul>
</div>
<div class="abs btn" style="left:796px;top:587px;width:189px;height:35px;font-size:11px;gap:10px">
  <svg width="22" height="12" viewBox="0 0 22 12"><rect x="1" y="1" width="13" height="7" fill="#fff"/><rect x="15" y="3" width="6" height="5" fill="#fff"/><circle cx="5" cy="10" r="2" fill="#fff"/><circle cx="18" cy="10" r="2" fill="#fff"/></svg>
  See all heavy duty</div>

<div class="abs section-title" style="left:131px;top:682px">Featured Ads</div>

<div class="abs ad" style="left:134px;top:722px"><div class="photo" role="img" aria-label="Orange mining dump truck under a blue sky" style="background:linear-gradient(135deg,#8fb3d8,#d9962b 55%,#6b5a3a)"></div><h4>Truck Heading 1</h4><div class="price">$24,900.00</div><div class="loc">Clear Lake, IA</div></div>
<div class="abs ad" style="left:341px;top:722px"><div class="photo" role="img" aria-label="Blue light-duty cab truck in a parking lot" style="background:linear-gradient(135deg,#c9cfd8,#3a5fa8 55%,#5c5f66)"></div><h4>Truck Heading 2</h4><div class="price">$32.5890.00</div><div class="loc">Clear Lake, IA</div></div>
<div class="abs ad" style="left:549px;top:722px"><div class="photo" role="img" aria-label="Vintage teal pickup truck on grass" style="background:linear-gradient(135deg,#a9c6d8,#3f8a8a 50%,#5d7a3a)"></div><h4>Truck Heading 3</h4><div class="price">$24,900.00</div><div class="loc">Clear Lake, IA</div></div>
<div class="abs ad" style="left:134px;top:1010px"><div class="photo" role="img" aria-label="White semi trailer truck on a highway" style="background:linear-gradient(160deg,#9fc3e6,#e6e8ea 55%,#4c5a4a)"></div><h4>Truck Heading 4</h4><div class="price">$24,900.00</div><div class="loc">Clear Lake, IA</div></div>
<div class="abs ad" style="left:341px;top:1010px"><div class="photo" role="img" aria-label="Blue tractor unit with white trailer" style="background:linear-gradient(135deg,#b9d2ea,#2f6fb0 55%,#6d7277)"></div><h4>Truck Heading 5</h4><div class="price">$125,562.00</div><div class="loc">Clear Lake, IA</div></div>
<div class="abs ad" style="left:549px;top:1010px"><div class="photo" role="img" aria-label="Green and yellow dump truck front view" style="background:linear-gradient(135deg,#cfd6dc,#2f8a6a 50%,#c9a63a)"></div><h4>Truck Heading 6</h4><div class="price">$24,900.00</div><div class="loc">Clear Lake, IA</div></div>

<div class="abs section-title" style="left:756px;top:682px">Trucks for sale by state</div>
<div class="abs box" style="left:756px;top:722px;width:312px;height:378px"></div>
<div class="abs links" style="left:778px;top:739px;grid-template-columns:91px 99px 100px">
  <a>Alabama</a><a>Indiana</a><a>Nebraska</a>
  <a>Alaska</a><a>Iowa</a><a>Nevada</a>
  <a>Arizona</a><a>Kansas</a><a>New Hampshire</a>
  <a>Arkansas</a><a>Kentucky</a><a>New Jersey</a>
  <a>California</a><a>Lousiana</a><a>New Mexico</a>
  <a>Colorado</a><a>Maine</a><a>New York</a>
  <a>Connecticut</a><a>Maryland</a><a>North Carolina</a>
  <a>Delaware</a><a>Massachusetts</a><a>North Dakota</a>
  <a>Florida</a><a>Michigan</a><a>Ohio</a>
  <a>Georgia</a><a>Minnesota</a><a>Oklahoma</a>
  <a>Hawaii</a><a>Mississippi</a><a>Oregon</a>
  <a>Idaho</a><a>Missouri</a><a>Pennsylvania</a>
  <a>Illinois</a><a>Montana</a><a></a>
</div>
<div class="abs btn small-btn" style="left:979px;top:1060px;width:75px">View more</div>

<div class="abs section-title" style="left:756px;top:1135px">Trucks for sale by make</div>
<div class="abs box" style="left:756px;top:1176px;width:312px;height:181px"></div>
<div class="abs links" style="left:778px;top:1192px;grid-template-columns:91px 99px 100px">
  <a>Ironford</a><a>Intercity</a><a>Isaro</a>
  <a>Freightwell</a><a>Kenridge</a><a>Mackley</a>
  <a>Chevalia</a><a>Rovan</a><a>Volvane</a>
  <a>Peterhaul</a><a>Gemline</a><a>Dodway</a>
  <a>Hinara</a><a>Sterlow</a><a>Mercer-Bauer</a>
</div>
<div class="abs btn small-btn" style="left:979px;top:1319px;width:75px">View more</div>

<div class="abs box" style="left:134px;top:1309px;width:603px;height:348px"></div>
<div class="abs section-title" style="left:169px;top:1333px;font-size:15px">Latest Blog</div>
<div class="abs btn small-btn" style="left:647px;top:1334px;width:69px;height:20px;font-size:9px">View all</div>
<div class="abs" role="img" aria-label="Dark semi truck parked at a depot" style="left:168px;top:1388px;width:108px;height:87px;background:linear-gradient(135deg,#b8c4cf,#2c3440 60%,#7a7f86)"></div>
<div class="abs blog-item" style="left:306px;top:1382px;width:410px">
  <div class="date">10/12/2016</div>
  <h5>Contrary to popular belief, Lorem Ipsum is not simply</h5>
  <p>There are many variations of passages of Lorem Ipsum available, but the majority have suffered alteration in some form.</p>
</div>
<div class="abs" style="left:168px;top:1503px;width:540px;height:1px;background:var(--line)"></div>
<div class="abs" role="img" aria-label="Green tow truck parked outdoors" style="left:168px;top:1529px;width:108px;height:89px;background:linear-gradient(135deg,#9fb37a,#2f4a2a 55%,#c8b04a)"></div>
<div class="abs blog-item" style="left:306px;top:1523px;width:410px">
  <div class="date">10/12/2016</div>
  <h5>It is a long established fact that a reader</h5>
  <p>Sed ut perspiciatis unde omnis iste natus error sit voluptatem accusantium doloremque laudantium, totam rem aperiam.</p>
</div>

<div class="abs" role="img" aria-label="Row of red and blue semi trucks parked under a blue sky" style="left:759px;top:1382px;width:309px;height:275px;background:linear-gradient(100deg,#b8383a 0%,#c85a5a 40%,#5f8fc9 70%,#9cc0e4 100%)"></div>
<div class="abs" style="left:759px;top:1455px;width:309px;text-align:center;color:#fff;font-weight:700;font-size:24px;line-height:1.2">MORE TRUCKS<br>AVAILABLE</div>
<div class="abs btn" style="left:850px;top:1544px;width:125px;height:40px;font-size:14px">Read more</div>

<div class="abs footer"></div>
<div class="abs logo" style="left:131px;top:1783px">Ridgeline trucks</div>
<div class="abs label-title" style="left:196px;top:1879px;font-size:13px">Follow us</div>
<div class="abs social" style="left:176px;top:1921px"></div>
<div class="abs social" style="left:220px;top:1921px"></div>
<div class="abs social" style="left:265px;top:1921px"></div>

<div class="abs label-title" style="left:434px;top:1756px;font-size:13px">Chatter</div>
<div class="abs" style="left:437px;top:1798px;width:304px;height:271px;background:var(--white)"></div>
<div class="abs tweet" style="left:437px;top:1819px;width:304px;padding-left:78px">
  <span class="dot"><i></i></span><span class="when">3 May</span>
  <h6>HEADING 1</h6><p>Sed ut perspiciatis unde omnis iste<br>natus error sit voluptatem.</p></div>
<div class="abs tweet" style="left:437px;top:1906px;width:304px;padding-left:78px">
  <span class="dot"><i></i></span><span class="when">3 May</span>
  <h6>HEADING 2</h6><p>Sed ut perspiciatis unde omnis iste<br>natus error sit voluptatem.</p></div>
<div class="abs tweet" style="left:437px;top:1994px;width:304px;padding-left:78px">
  <span class="dot"><i></i></span><span class="when">3 May</span>
  <h6>HEADING 3</h6><p>Sed ut perspiciatis unde omnis iste<br>natus error sit voluptatem.</p></div>

<div class="abs label-title" style="left:806px;top:1756px;font-size:13px">Find a dealer</div>
<div class="abs" style="left:806px;top:1797px;width:270px;font-size:11px;line-height:1.95;color:#555">Sed ut perspiciatis unde omnis iste natus error sit voluptatem accusantium</div>
<div class="abs" role="img" aria-label="Grey map of the United States" style="left:809px;top:1882px;width:250px;height:147px;background:#c9cbcd;border-radius:40px 60px 30px 50px"></div>
<div class="abs btn" style="left:853px;top:1931px;width:129px;height:37px;font-size:12px">Find a dealer</div>

<div class="abs" style="left:131px;top:2118px;width:937px;height:1px;background:#ddd"></div>
<div class="abs foot-links" style="left:130px;top:2159px">Home &nbsp;|&nbsp; About us &nbsp;|&nbsp; Sell &nbsp;|&nbsp; Feedback &nbsp;|&nbsp; Contact us</div>
<div class="abs foot-links" style="right:135px;top:2159px">Copyrights @ 2016 All Rights Reserved</div>

</body>
</html>
```